Artsy 1 Page Website/Brochure for climate change investment company

We want art like feel similar to https://velmora.quintrel.net/ for a 1 page online website (1 page) to have an online presence. We want to show credibility, no functionality. The only call to action is an email to the company.
3 sections 1) Company 2) Services, 3) brands.
The idea is 1) we are credible and serious, 2) market is increasing, 3) knowledge about sector, 4) large branded companies in the sector.
We want users to be interested and want to learn more.
There should be 1 or 2 animated sections. 1) GHG (green house gases) floating up or something showing emissions rising, 2) Services can scroll or loop.
See my mockup. The font should be standardized. The text shapes should be same. Keep same color palette unless you have better idea.
https://slides.brovanta.com/deck/7KxQ2mPzT9wLbV4nRfYcHd8sJuA6eGtNqXoZ1iMvBkE/view?ref=share
Logo for company AirLedgerHub.com

Target Market(s)

Potential Investors and Academics and Industry specialist. This is not for general consumers

Industry/Entity Type

Environment/Investors

Number of Pages Required

1 page

Requirements
Must have
• Artsy feel like a brochure
Should not have
• I do not want a functional website with lots of standard menus e.g. menus at the top

```html
<!DOCTYPE html>
<html lang="en">
<head>
<meta charset="utf-8">
<title>AirLedgerHub – One Page Brochure</title>
<link rel="stylesheet" href="https://fonts.googleapis.com/css2?family=Poppins:wght@400;500;600;700&family=Saira+Condensed:wght@600;700&display=swap">
<style>
  :root{
    --stage:#ebebeb;
    --magenta:#c8104f;
    --charcoal:#232323;
    --slate:#5a5a5a;
    --olive:#797362;
    --column:#2b2b2b;
    --column-text:#b2ad9a;
    --space:#474747;
    --logo:#8d8d8d;
    --white:#ffffff;
  }
  *{box-sizing:border-box;margin:0;padding:0}
  html,body{width:1200px;height:267px;overflow:hidden;background:var(--stage)}
  body{position:relative;font-family:"Poppins",sans-serif;color:var(--white)}
  .panel{position:absolute;top:20px;width:372px;height:220px;overflow:hidden}
  .panel--home{left:15px;background:var(--magenta)}
  .panel--services{left:415px;background:var(--olive)}
  .panel--space{left:814px;background:var(--space)}

  .tab{position:absolute;top:0;height:100%;width:24.5px}
  .tab--home{background:var(--magenta)}
  .tab--services{background:var(--charcoal)}
  .tab--space{background:var(--slate)}
  .tab__icon{position:absolute;top:5px;left:2.5px;width:19.5px;height:19.5px}
  .tab__label{position:absolute;left:50%;top:50%;transform:translate(-50%,-50%) rotate(-90deg);
    font-weight:700;font-size:13px;letter-spacing:.3px;white-space:nowrap;line-height:1}
  .tab__number{position:absolute;bottom:5px;left:0;width:100%;text-align:center;font-weight:700;font-size:11px;line-height:1}

  .home-strip{position:absolute;left:0;top:0;width:24px;height:100%;border-right:.5px solid rgba(255,255,255,.25)}
  .home-art{position:absolute;left:24px;top:0;width:301px;height:100%;
    background:linear-gradient(180deg,#c61552 0%,#b10f46 45%,#8c0a33 100%)}
  .home-watermark{position:absolute;left:2px;bottom:40px;font-weight:700;font-size:130px;line-height:1;color:rgba(90,0,25,.18);letter-spacing:-4px}
  .home-watermark span{font-size:80px}
  .home-title{position:absolute;left:24px;width:301px;top:10px;text-align:center;font-weight:600;font-size:16px;line-height:1.3}
  .home-email{position:absolute;left:24px;width:301px;top:34px;text-align:center;font-size:4.5px}
  .gas-pills{position:absolute;left:33px;top:79px;display:flex;flex-direction:column;gap:3px}
  .gas-pill{width:11px;height:20px;border:.6px solid rgba(255,255,255,.9);border-radius:3px;
    display:flex;align-items:center;justify-content:center}
  .gas-pill span{transform:rotate(-90deg);font-size:5.5px;font-weight:600;white-space:nowrap;line-height:1}
  .ghg-visual{position:absolute;left:112px;top:62px;width:150px;height:148px;
    background:radial-gradient(ellipse 60% 55% at 50% 45%,rgba(255,255,255,.35) 0%,rgba(255,255,255,.12) 60%,rgba(255,255,255,0) 100%)}
  .ghg-label{position:absolute;left:112px;width:150px;top:88px;text-align:center;font-weight:600;font-size:7px}
  .footer{position:absolute;bottom:8px;font-size:3.2px;letter-spacing:.1px;text-align:center}

  .service-col{position:absolute;top:18px;width:61.5px;height:174px;background:var(--column);
    font-family:"Saira Condensed",sans-serif;font-weight:700;color:var(--column-text);text-align:center;
    font-size:10px;line-height:10.5px;letter-spacing:.2px}
  .service-col__top{position:absolute;top:19px;left:0;width:100%}
  .service-col__bottom{position:absolute;top:126px;left:0;width:100%}
  .service-hover{position:absolute;left:100.5px;top:23px;width:61px;height:61px;border-radius:50%;background:rgba(200,196,172,.55)}

  .space-title{position:absolute;left:73.6px;right:0;top:9px;text-align:center;font-weight:700;font-size:16px;letter-spacing:.5px}
  .space-watermark{position:absolute;left:73.6px;right:0;top:95px;text-align:center;font-weight:700;font-size:24px;color:rgba(0,0,0,.08);letter-spacing:1px}
  .partner-grid{position:absolute;left:82px;top:30px;width:282px;height:180px;display:grid;
    grid-template-columns:repeat(4,1fr);grid-template-rows:repeat(4,1fr)}
  .partner{display:flex;align-items:center;justify-content:center;gap:3px;font-weight:500;font-size:8px;color:var(--logo);
    border-right:.5px solid rgba(255,255,255,.05);border-bottom:.5px solid rgba(255,255,255,.05);text-align:center;line-height:1.05}
  .partner:nth-child(4n){border-right:none}
  .partner:nth-child(n+13){border-bottom:none}
  .partner__mark{width:7px;height:7px;border-radius:50%;background:var(--logo);flex:none}

  .pager{position:absolute;width:10px;height:10px;border:.6px solid #9a9a9a;border-radius:50%;display:flex;align-items:center;justify-content:center}
  .pager svg{width:8px;height:8px;display:block}
</style>
</head>
<body>

<section class="panel panel--home">
  <div class="home-art" role="img" aria-label="Misty pine forest photograph tinted deep magenta"></div>
  <div class="home-strip"></div>
  <svg class="tab__icon" viewBox="0 0 20 20" aria-hidden="true"><circle cx="10" cy="10" r="9" fill="none" stroke="#fff" stroke-width=".8"/><circle cx="9" cy="8" r="2.3" fill="none" stroke="#fff" stroke-width=".8"/><path d="M5 14.5c.6-2.4 2.2-3.4 4-3.4s3.4 1 4 3.4" fill="none" stroke="#fff" stroke-width=".8"/><path d="M13.5 7.5h3M15 6v3" stroke="#fff" stroke-width=".8"/></svg>
  <div class="home-watermark">CO<span>2</span></div>
  <span class="tab__label" style="left:12px">HOME</span>
  <span class="tab__number" style="width:24px">01</span>

  <h1 class="home-title">AirLedgerHub</h1>
  <p class="home-email">✉ Email : partners@airledgerhub.com</p>

  <div class="gas-pills">
    <div class="gas-pill"><span>CH₄↑</span></div>
    <div class="gas-pill"><span>GHG↑</span></div>
    <div class="gas-pill"><span>CO₂↑</span></div>
  </div>

  <div class="ghg-visual" role="img" aria-label="Illustration of a greenhouse gas droplet releasing smaller drops into a pool"></div>
  <p class="ghg-label">GHGs</p>

  <p class="footer" style="left:24px;width:301px">© 2022 AIRLEDGERHUB. ALL RIGHTS RESERVED</p>

  <div class="tab tab--services" style="left:325px">
    <svg class="tab__icon" viewBox="0 0 20 20" aria-hidden="true"><circle cx="10" cy="10" r="9" fill="none" stroke="#fff" stroke-width=".8"/><circle cx="10" cy="10" r="4.5" fill="none" stroke="#fff" stroke-width=".8" stroke-dasharray="1.6 1"/><circle cx="10" cy="10" r="1.8" fill="none" stroke="#fff" stroke-width=".8"/></svg>
    <span class="tab__label">SERVICES</span><span class="tab__number">02</span>
  </div>
  <div class="tab tab--space" style="left:349.5px;width:22.5px">
    <svg class="tab__icon" style="left:1.5px" viewBox="0 0 20 20" aria-hidden="true"><circle cx="10" cy="10" r="9" fill="none" stroke="#fff" stroke-width=".8"/><circle cx="10" cy="8.5" r="3" fill="none" stroke="#fff" stroke-width=".8"/><path d="M8 11l-1.5 4 3.5-1.5 3.5 1.5L12 11" fill="none" stroke="#fff" stroke-width=".8"/></svg>
    <span class="tab__label">OUR SPACE</span><span class="tab__number">03</span>
  </div>
</section>

<div class="pager" style="left:396px;top:123px"><svg viewBox="0 0 10 10"><path d="M4 3l2 2-2 2" fill="none" stroke="#777" stroke-width=".8"/></svg></div>
<div class="pager" style="left:396px;top:134px"><svg viewBox="0 0 10 10"><path d="M6 3L4 5l2 2" fill="none" stroke="#777" stroke-width=".8"/></svg></div>

<section class="panel panel--services">
  <div class="tab tab--home" style="left:0">
    <svg class="tab__icon" viewBox="0 0 20 20" aria-hidden="true"><circle cx="10" cy="10" r="9" fill="none" stroke="#fff" stroke-width=".8"/><circle cx="9" cy="8" r="2.3" fill="none" stroke="#fff" stroke-width=".8"/><path d="M5 14.5c.6-2.4 2.2-3.4 4-3.4s3.4 1 4 3.4" fill="none" stroke="#fff" stroke-width=".8"/><path d="M13.5 7.5h3M15 6v3" stroke="#fff" stroke-width=".8"/></svg>
    <span class="tab__label">HOME</span><span class="tab__number">01</span>
  </div>
  <div class="tab tab--services" style="left:24.5px">
    <svg class="tab__icon" viewBox="0 0 20 20" aria-hidden="true"><circle cx="10" cy="10" r="9" fill="none" stroke="#fff" stroke-width=".8"/><circle cx="10" cy="10" r="4.5" fill="none" stroke="#fff" stroke-width=".8" stroke-dasharray="1.6 1"/><circle cx="10" cy="10" r="1.8" fill="none" stroke="#fff" stroke-width=".8"/></svg>
    <span class="tab__label">SERVICES</span><span class="tab__number">02</span>
  </div>

  <div class="service-col" style="left:67px"><div class="service-col__top">CARBON<br>CAPTURE</div><div class="service-col__bottom">NATURE<br>BASED<br>SOLUTIONS</div></div>
  <div class="service-col" style="left:135.5px"><div class="service-col__top">TECHNOLOGY<br>BASED<br>SOLUTIONS</div><div class="service-col__bottom">PERMANENT<br>CARBON<br>REMOVAL</div></div>
  <div class="service-col" style="left:203.5px"><div class="service-col__top">NEW<br>METHODO-<br>LOGIES</div><div class="service-col__bottom">REDD+</div></div>
  <div class="service-col" style="left:271.5px"><div class="service-col__top">STREAMING</div><div class="service-col__bottom">CARBON<br>MARKETS</div></div>
  <div class="service-hover"></div>

  <p class="footer" style="left:48.5px;width:300px">© 2022 AIRLEDGERHUB. ALL RIGHTS RESERVED</p>

  <div class="tab tab--space" style="left:349px;width:23px">
    <svg class="tab__icon" style="left:1.5px" viewBox="0 0 20 20" aria-hidden="true"><circle cx="10" cy="10" r="9" fill="none" stroke="#fff" stroke-width=".8"/><circle cx="10" cy="8.5" r="3" fill="none" stroke="#fff" stroke-width=".8"/><path d="M8 11l-1.5 4 3.5-1.5 3.5 1.5L12 11" fill="none" stroke="#fff" stroke-width=".8"/></svg>
    <span class="tab__label">OUR SPACE</span><span class="tab__number">03</span>
  </div>
</section>

<div class="pager" style="left:795px;top:123px"><svg viewBox="0 0 10 10"><path d="M4 3l2 2-2 2" fill="none" stroke="#777" stroke-width=".8"/></svg></div>
<div class="pager" style="left:795px;top:134px"><svg viewBox="0 0 10 10"><path d="M6 3L4 5l2 2" fill="none" stroke="#777" stroke-width=".8"/></svg></div>

<section class="panel panel--space">
  <div class="tab tab--home" style="left:0">
    <svg class="tab__icon" viewBox="0 0 20 20" aria-hidden="true"><circle cx="10" cy="10" r="9" fill="none" stroke="#fff" stroke-width=".8"/><circle cx="9" cy="8" r="2.3" fill="none" stroke="#fff" stroke-width=".8"/><path d="M5 14.5c.6-2.4 2.2-3.4 4-3.4s3.4 1 4 3.4" fill="none" stroke="#fff" stroke-width=".8"/><path d="M13.5 7.5h3M15 6v3" stroke="#fff" stroke-width=".8"/></svg>
    <span class="tab__label">HOME</span><span class="tab__number">01</span>
  </div>
  <div class="tab tab--services" style="left:24.5px">
    <svg class="tab__icon" viewBox="0 0 20 20" aria-hidden="true"><circle cx="10" cy="10" r="9" fill="none" stroke="#fff" stroke-width=".8"/><circle cx="10" cy="10" r="4.5" fill="none" stroke="#fff" stroke-width=".8" stroke-dasharray="1.6 1"/><circle cx="10" cy="10" r="1.8" fill="none" stroke="#fff" stroke-width=".8"/></svg>
    <span class="tab__label">SERVICES</span><span class="tab__number">02</span>
  </div>
  <div class="tab tab--space" style="left:49px">
    <svg class="tab__icon" viewBox="0 0 20 20" aria-hidden="true"><circle cx="10" cy="10" r="9" fill="none" stroke="#fff" stroke-width=".8"/><circle cx="10" cy="8.5" r="3" fill="none" stroke="#fff" stroke-width=".8"/><path d="M8 11l-1.5 4 3.5-1.5 3.5 1.5L12 11" fill="none" stroke="#fff" stroke-width=".8"/></svg>
    <span class="tab__label">OUR SPACE</span><span class="tab__number">03</span>
  </div>

  <h2 class="space-title">OUR SPACE</h2>
  <div class="space-watermark">AIRLEDGERHUB</div>

  <div class="partner-grid">
    <div class="partner"><span class="partner__mark"></span>Terrava</div>
    <div class="partner">Voltrix</div>
    <div class="partner"><span class="partner__mark"></span>Emission<br>Accord</div>
    <div class="partner">Cartwell</div>
    <div class="partner">Paylume</div>
    <div class="partner">Searchly</div>
    <div class="partner">Union<br>Council</div>
    <div class="partner">Peakline</div>
    <div class="partner">Verdmark</div>
    <div class="partner">Climate<br>Panel</div>
    <div class="partner">GridPact Inc.</div>
    <div class="partner"><span class="partner__mark"></span>Summit 2021</div>
    <div class="partner">Carbon<br>Rollbook</div>
    <div class="partner">Skyoffset</div>
    <div class="partner"><span class="partner__mark"></span>Action<br>Ledger</div>
    <div class="partner">Risk Forum</div>
  </div>

  <p class="footer" style="left:73.6px;width:298px">© 2022 AIRLEDGERHUB. ALL RIGHTS RESERVED</p>
</section>

</body>
</html>
```